Business Name: DM Space Arranging Pty Ltd

Business Type: Professional Home Styling and Minor Renovation Business

Logo: Attached is the logo that has been created.
I always envisaged the logo in the middle of the business card with my full name underneath it.

Marnie Tulloch B.Com LMR HTV
Property Stylist & Project Manager

Include dot points of services
Staging Houses for Sale
Minor Home Renovations
Home Styling & Project Management
Re-Designing Living Spaces to Aid the Disabled

Somewhere on the card I would like to incorporate
"Property Styling and Cosmetic Renovations"

Colour Scheme:
Gloss black business card, with white and then
Gold or Silver as the highlight colours.

Incorporate a small amount of yellow only if possible to make it pop. If this really doesn’t work it doesn’t have to be used. Also l like the colour teal if that needs to be used as a contrast colour.

Feel/Themes
• I love antique chairs, regal expensive looking furniture mixed with modern homes (this is the unique style I want to sell) antique and modern mix that looks high class as well as modern and fresh, targeting an executive market.
• I want to use an orchid as a trademark throughout the course of my work, not sure if this can somehow be incorporated? Also really like crowns to give that regal/antique feel and then something else to give that modern twist (I don’t know what the something else could be)
• Wall Paper Look (on a portion of it not all of it, like a French look)
• Overall feel - A very deluxe and professional feel with a little bit of creative flare.

I hope this helps create a bit of a picture.

Is it ok that I call you tomorrow morning? My mobile number is 0438 926 574 if you have any questions for me in the meantime.

Target Market(s)

High Quality Executive Market - People selling homes

Industry/Entity Type

Business

Contact Information for Business Card

Include dot points of services:
Staging Houses for Sale
Minor Home Renovations

Font styles to use
Serif
Script

Colors
33b8a4
fbed22

Requirements
Must have
• Marnie Tulloch B.Com LMR HTV
• Property Stylist & Project Manager
• LMR and HTV Logos on the card
• "Dramatically increase the value of your property"
Nice to have
• Colour Scheme:
• Gloss black business card, with white and then
• Gold or Silver as the highlight colours.
• Incorporate a small amount of yellow only if possible to make it pop. If this really doesn’t work it doesn’t have to be used. Also l like the colour teal if that needs to be used as a contrast colour.
• Also like teal as a highlight colour.

```html
<!DOCTYPE html>
<html lang="en">
<head>
<meta charset="utf-8">
<title>DM Space Arranging Pty Ltd — Business Card</title>
<link rel="stylesheet" href="https://fonts.googleapis.com/css2?family=Great+Vibes&family=Old+Standard+TT:ital,wght@0,400;1,400&family=Roboto+Condensed:wght@400&display=swap">
<style>
  :root{
    --backdrop:#2a2a2c;
    --card-white:#ffffff;
    --gloss-black:#0d0d0e;
    --gold-light:#f3d98a;
    --gold:#c9a13f;
    --gold-deep:#8a6a1e;
    --silver:#b9b9b9;
    --silver-soft:#e4e4e4;
    --ink:#2b2b2b;
    --ink-light:#cfcfcf;
    --teal:#33b8a4;
  }
  *{box-sizing:border-box;margin:0;padding:0}
  html,body{width:1200px;height:852px;overflow:hidden;background:var(--backdrop)}
  .stage{position:relative;width:1200px;height:852px}
  .card{position:absolute;width:520px;height:300px;border-radius:12px;overflow:hidden;background:var(--card-white);box-shadow:0 14px 30px rgba(0,0,0,.45)}
  .card--front{left:50px;top:150px}
  .card--back{left:630px;top:402px}
  .card__shapes{position:absolute;inset:0;width:100%;height:100%}

  .ornament{position:absolute;border-radius:50%;background:radial-gradient(ellipse at center,var(--silver-soft) 0%,rgba(228,228,228,.55) 45%,rgba(255,255,255,0) 72%)}
  .card--front .ornament{left:120px;top:40px;width:260px;height:170px}
  .wordmark{position:absolute;font-family:"Old Standard TT",serif;font-size:15px;letter-spacing:.14em;text-transform:uppercase;color:var(--ink);white-space:nowrap;border-top:1px solid var(--ink);border-bottom:1px solid var(--ink);padding:3px 8px}
  .card--front .wordmark{left:130px;top:112px}

  .card--back .ornament{left:20px;top:60px;width:150px;height:180px}
  .card--back .wordmark{font-size:11px;left:95px;top:150px;transform:translate(-50%,-50%) rotate(90deg)}

  .holder{position:absolute;left:278px;top:62px}
  .holder__name{font-family:"Great Vibes",cursive;font-size:30px;color:var(--teal);line-height:1}
  .holder__credentials,.holder__role{font-family:"Old Standard TT",serif;font-size:12px;color:var(--ink-light);line-height:1.3}
  .holder__role{font-style:italic}
  .services{position:absolute;left:290px;top:140px;list-style:none;font-family:"Old Standard TT",serif;font-size:12.5px;color:var(--ink-light);line-height:1.45}
  .services li::before{content:"»";margin-right:8px}
  .tagline{position:absolute;right:22px;top:258px;font-family:"Roboto Condensed",sans-serif;font-size:13px;color:var(--gloss-black)}
</style>
</head>
<body>
<main class="stage">

  <section class="card card--front" aria-label="Card front">
    <svg class="card__shapes" viewBox="0 0 520 300" preserveAspectRatio="none" aria-hidden="true">
      <defs>
        <linearGradient id="gold-front" x1="0" y1="0" x2="1" y2="0">
          <stop offset="0" stop-color="var(--gold-deep)"/>
          <stop offset=".45" stop-color="var(--gold-light)"/>
          <stop offset=".75" stop-color="var(--gold)"/>
          <stop offset="1" stop-color="var(--gold-deep)"/>
        </linearGradient>
      </defs>
      <path d="M0 300 L0 288 C180 266 360 232 520 204 L520 300 Z" fill="url(#gold-front)"/>
      <path d="M0 300 L0 293 C120 286 260 286 430 300 Z" fill="var(--gloss-black)"/>
    </svg>
    <div class="ornament" role="img" aria-label="Faint silver flourish ornament behind the company name"></div>
    <p class="wordmark">DM Space Arranging Pty Ltd</p>
  </section>

  <section class="card card--back" aria-label="Card back">
    <svg class="card__shapes" viewBox="0 0 520 300" preserveAspectRatio="none" aria-hidden="true">
      <defs>
        <linearGradient id="gold-back" x1="0" y1="0" x2="1" y2="0">
          <stop offset="0" stop-color="var(--gold-deep)"/>
          <stop offset=".35" stop-color="var(--gold-light)"/>
          <stop offset=".7" stop-color="var(--gold)"/>
          <stop offset="1" stop-color="var(--gold-light)"/>
        </linearGradient>
      </defs>
      <path d="M186 0 H520 V300 H252 C236 200 262 110 186 0 Z" fill="var(--gloss-black)"/>
      <path d="M186 0 C262 110 236 200 252 300" fill="none" stroke="url(#gold-back)" stroke-width="5"/>
      <path d="M238 228 H520 V300 H252 C246 272 240 250 238 228 Z" fill="url(#gold-back)"/>
    </svg>
    <div class="ornament" role="img" aria-label="Faint silver flourish ornament behind the company name"></div>
    <p class="wordmark">DM Space Arranging Pty Ltd</p>

    <div class="holder">
      <p class="holder__name">Marnie Tulloch</p>
      <p class="holder__credentials">B.Com LMR HTV</p>
      <p class="holder__role">Property Stylist &amp; Project Manager</p>
    </div>
    <ul class="services">
      <li>Staging Houses for Sale</li>
      <li>Minor Home Renovations</li>
      <li>Home Styling &amp; Project Management</li>
      <li>Re-Designing Living</li>
      <li>Spaces to Aid the Disabled</li>
    </ul>
    <p class="tagline">Property Styling &amp; Cosmetic Renovations</p>
  </section>

</main>
</body>
</html>
```